Business Card Design for Occupational Medicine Start Up Company

We need to design a professional business card. We are a healthcare company providing occupational medicine services to blue collar industries. We are professional, efficient and high quality service providers.

Target Market(s)

Blue Collar Industry: Shipbuilding, Ports, Trucking Companies; The Executives and Safety Officers for these companies

Industry/Entity Type

Healthcare

Contact Information for Business Card

Logo, Name, Title, Email, Phone

Other font styles liked:
• Please match our Brand Guide

Requirements
Must have
• Our Company Colors and Logo

```html
<!DOCTYPE html>
<html lang="en">
<head>
<meta charset="utf-8">
<title>Harborline Health – Business Card</title>
<link rel="stylesheet" href="https://fonts.googleapis.com/css2?family=Arimo:wght@400;700&display=swap">
<style>
  :root {
    --backdrop: #9a9a9a;
    --navy: #2b3580;
    --sky: #29a9e1;
    --orange: #f5b04c;
    --white: #ffffff;
    --back-blue: #24a8e0;
    --cyan-light: #3ef0fb;
    --blue-deep: #0a5fd0;
  }
  * { margin: 0; padding: 0; box-sizing: border-box; }
  html, body {
    width: 1133px; height: 1200px; overflow: hidden;
    background: var(--backdrop);
    font-family: "Arimo", Arial, sans-serif;
  }
  .card {
    position: absolute; left: 200px;
    width: 725px; height: 412px; overflow: hidden;
  }
  .card-front { top: 144px; background: var(--white); }
  .card-back { top: 640px; background: var(--back-blue); }
  .wave { position: absolute; inset: 0; width: 725px; height: 412px; }
  .contact { position: absolute; left: 40px; top: 30px; color: var(--white); }
  .contact-name { font-size: 22px; font-weight: 700; color: var(--sky); line-height: 1.2; }
  .contact-title { font-size: 16px; margin-top: 3px; }
  .contact-address { font-size: 16px; line-height: 21px; margin-top: 9px; }
  .contact-list { list-style: none; margin-top: 7px; font-size: 16px; line-height: 21px; }
  .contact-list li { display: flex; align-items: center; gap: 8px; }
  .contact-list svg { width: 12px; height: 12px; flex: none; }
  .brand {
    position: absolute; transform: translateX(-50%);
    display: flex; flex-direction: column; align-items: center; gap: 16px;
    white-space: nowrap;
  }
  .brand-front { top: 226px; left: 534px; }
  .brand-back { top: 312px; left: 536px; }
  .brand-dot { width: 56px; height: 56px; border-radius: 50%; background: var(--navy); }
  .brand-name { font-size: 27px; font-weight: 700; letter-spacing: 1px; }
  .brand-front .brand-name { color: var(--navy); }
  .brand-back .brand-name { color: var(--white); }
  .back-graphic {
    position: absolute; left: 0; top: 0;
    width: 388px; height: 412px;
    border-radius: 0 190px 190px 0;
    background: linear-gradient(90deg, var(--cyan-light) 0%, #22b6f5 45%, var(--blue-deep) 100%);
    opacity: 0.85;
  }
</style>
</head>
<body>
  <section class="card card-front">
    <svg class="wave" viewBox="0 0 725 412" aria-hidden="true">
      <path d="M0,0 H725 V70 C640,42 585,72 515,142 C440,217 330,314 210,306 C130,300 60,264 0,232 Z" fill="var(--sky)"/>
      <path d="M0,0 H725 V58 C640,30 580,60 510,132 C435,210 330,308 210,302 C130,297 60,263 0,234 Z" fill="var(--white)"/>
      <path d="M0,0 H725 V26 C640,10 575,40 505,115 C430,198 320,300 210,298 C130,296 60,266 0,240 Z" fill="var(--orange)"/>
      <path d="M0,0 H725 V20 C640,4 572,34 500,110 C425,192 315,290 205,288 C125,286 60,250 0,214 Z" fill="var(--navy)"/>
    </svg>
    <div class="contact">
      <p class="contact-name">Daniel Reyes</p>
      <p class="contact-title">President</p>
      <p class="contact-address">214 Cedar Wharf Road<br>Seaport, Maine 04112</p>
      <ul class="contact-list">
        <li><svg viewBox="0 0 12 12"><path d="M2.5 1 L4.5 1 L5 3.5 L3.8 4.5 C4.5 6 6 7.5 7.5 8.2 L8.5 7 L11 7.5 L11 9.5 C11 10.5 10 11 9 11 C5 10.5 1.5 7 1 3 C1 2 1.5 1 2.5 1Z" fill="var(--sky)"/></svg>555-310-4826</li>
        <li><svg viewBox="0 0 12 12"><rect x="3" y="0.5" width="6" height="11" rx="1" fill="none" stroke="var(--sky)" stroke-width="1.3"/></svg>555-720-1934</li>
        <li><svg viewBox="0 0 12 12"><rect x="0.5" y="2.5" width="11" height="7.5" fill="var(--sky)"/><path d="M0.5 2.5 L6 7 L11.5 2.5" fill="none" stroke="var(--navy)" stroke-width="1"/></svg>info@harborlinehealth.com</li>
        <li><svg viewBox="0 0 12 12"><circle cx="6" cy="6" r="5.5" fill="var(--sky)"/><path d="M3 4 C4 3 5 4 5 5 C5 6.5 4 7 4.5 9 M7 2 C7.5 3.5 9 4 10 4" fill="none" stroke="var(--navy)" stroke-width="1"/></svg>www.harborlinehealth.com</li>
      </ul>
    </div>
    <div class="brand brand-front">
      <span class="brand-dot"></span>
      <span class="brand-name">HARBORLINE HEALTH</span>
    </div>
  </section>

  <section class="card card-back">
    <div class="back-graphic" role="img" aria-label="Large brand symbol decoration in cyan to deep blue gradient"></div>
    <div class="brand brand-back">
      <span class="brand-name">HARBORLINE HEALTH</span>
    </div>
  </section>
</body>
</html>
```